Veltrano.co - Polar Expeditions Specialists

We need a modern, visually striking business card for Veltrano.co, a company specialized in selling expedition cruises to the most remote regions on Earth, with a focus on the Arctic and Antarctica. The design should instantly communicate that the cardholder is an expert in polar travel. Use clean, premium aesthetics with cool tones like icy blue and white, possibly incorporating polar imagery (ice, glaciers, penguins, etc.)

Attached the logo

Contact Information for Business Card

Feels high-end and trustworthy.. Visually memorable — encourages people to keep it

Colors
0054AA
0677BA
7BADD7
CADEEF
E8F1F8

Requirements
Must have
• ice, glaciers, penguins, montains
Nice to have
• modern, transparente,

```html
<!DOCTYPE html>
<html lang="en">
<head>
<meta charset="utf-8">
<title>Veltrano.co – Business Card</title>
<link rel="stylesheet" href="https://fonts.googleapis.com/css2?family=Poppins:wght@600;700&family=Arimo:wght@400;700&display=swap">
<style>
  :root {
    --backdrop: #9a9a9a;
    --card-white: #f7f7f7;
    --brand-blue: #2f6fb0;
    --accent-blue: #3a7cc2;
    --ink: #2a2a2a;
    --muted: #6b6b6b;
    --rule: #8a8a8a;
    --white: #ffffff;
  }
  * { box-sizing: border-box; margin: 0; padding: 0; }
  html, body { width: 1200px; height: 1050px; overflow: hidden; }
  body {
    background: var(--backdrop);
    position: relative;
    font-family: "Arimo", Arial, sans-serif;
  }
  .card {
    position: absolute;
    width: 700px;
    height: 400px;
    border-radius: 24px;
    overflow: hidden;
    box-shadow: 0 6px 18px rgba(0,0,0,0.18);
  }
  .card-front { left: 250px; top: 90px; background: var(--card-white); }
  .card-back { left: 250px; top: 560px; background: var(--brand-blue); }

  /* front: portrait layout turned on its side */
  .front-layout {
    position: absolute;
    width: 400px;
    height: 700px;
    left: 150px;
    top: -150px;
    transform: rotate(-90deg);
    display: flex;
    flex-direction: column;
    align-items: center;
    padding-top: 150px;
    text-align: center;
  }
  .front-wordmark {
    font-family: "Poppins", sans-serif;
    font-weight: 700;
    font-size: 30px;
    color: var(--accent-blue);
    margin-bottom: 70px;
  }
  .holder-name {
    font-family: "Arimo", sans-serif;
    font-weight: 700;
    font-size: 28px;
    color: var(--accent-blue);
    line-height: 1.1;
  }
  .holder-role {
    font-size: 18px;
    color: var(--muted);
    margin-top: 2px;
  }
  .divider {
    width: 70px;
    height: 1px;
    background: var(--rule);
    margin: 38px 0 30px;
  }
  .address {
    font-size: 18px;
    color: var(--ink);
    line-height: 1.45;
  }
  .contact-list {
    list-style: none;
    font-size: 18px;
    color: var(--ink);
    line-height: 1.45;
    text-align: left;
  }
  .contact-label {
    font-weight: 700;
    color: var(--accent-blue);
    margin-right: 6px;
  }

  /* back */
  .back-brand {
    position: absolute;
    inset: 0;
    display: flex;
    flex-direction: column;
    align-items: center;
    justify-content: center;
    color: var(--white);
  }
  .back-mark-dot {
    width: 46px;
    height: 46px;
    border-radius: 50%;
    background: var(--white);
    margin-bottom: 22px;
  }
  .back-wordmark {
    font-family: "Poppins", sans-serif;
    font-weight: 700;
    font-size: 62px;
    line-height: 1;
  }
  .back-tagline {
    font-family: "Poppins", sans-serif;
    font-weight: 600;
    font-size: 17px;
    letter-spacing: 0.5px;
    margin-top: 10px;
  }
</style>
</head>
<body>

<section class="card card-front" aria-label="Business card front">
  <div class="front-layout">
    <div class="front-wordmark">Veltrano.co</div>
    <div class="holder-name">Marcus Hale</div>
    <div class="holder-role">President</div>
    <div class="divider"></div>
    <p class="address">2170 Harbor Crest Lane<br>Glen Cove, NY 11542</p>
    <div class="divider"></div>
    <ul class="contact-list">
      <li><span class="contact-label">P :</span>(555) 3091-4476</li>
      <li><span class="contact-label">E :</span>name@veltrano.com</li>
      <li><span class="contact-label">W :</span>www.veltrano.com</li>
    </ul>
  </div>
</section>

<section class="card card-back" aria-label="Business card back">
  <div class="back-brand">
    <div class="back-mark-dot"></div>
    <div class="back-wordmark">Veltrano.co</div>
    <div class="back-tagline">Polar Expeditions Specialists</div>
  </div>
</section>

</body>
</html>
```